Road Construction Company needs business cards

We would like a new business card designed for our business.

We're a road construction company based in Qld, Australia.

Can the business card please have the following information on it.

Name: Warren Halbeck
Position: General Manager
Phone: 0472 915 348
Email: Warren.halbeck@tovrin.com.au
Address: 87 Marrow Ave, Pendlebay, QLD, 4023
Website: www.tovrin.com.au

Visually we'd like the card to be professional and simple.

Attached is our logo.

Our website is www.tovrin.com.au

Target Market(s)

Men aged 25-60

Contact Information for Business Card

As listed in project description

Font styles to use
Serif

Requirements
Must have
• Large logo on back of card

```html
<!DOCTYPE html>
<html lang="en">
<head>
<meta charset="utf-8">
<title>Tovrin – Business Card</title>
<link rel="stylesheet" href="https://fonts.googleapis.com/css2?family=Archivo+Black&family=Arimo:wght@400&display=swap">
<style>
  :root {
    --bg: #d9d9d9;
    --card-white: #ffffff;
    --navy: #0b4fa1;
    --sky: #33a6d9;
    --ink: #1b1b1b;
    --back-top: #33a8dc;
    --back-bottom: #0a4fa0;
  }
  * { box-sizing: border-box; margin: 0; padding: 0; }
  html, body {
    width: 1200px; height: 800px; overflow: hidden;
    background: var(--bg);
  }
  .canvas {
    width: 1200px; height: 800px;
    display: flex; align-items: center; justify-content: center; gap: 40px;
  }
  .card {
    position: relative;
    width: 540px; height: 310px;
    border-radius: 18px;
    overflow: hidden;
    box-shadow: 0 10px 28px rgba(0,0,0,0.22);
  }

  /* Front */
  .card--front { background: var(--card-white); }
  .holder { position: absolute; left: 40px; top: 46px; }
  .holder__name {
    font-family: "Archivo Black", sans-serif;
    font-size: 25px; letter-spacing: 1px;
    color: var(--navy); text-transform: uppercase; line-height: 1;
  }
  .holder__role {
    font-family: "Arimo", sans-serif;
    font-size: 18px; color: var(--sky); margin-top: 6px;
  }
  .contact-band {
    position: absolute; left: 0; top: 122px;
    width: 318px; height: 92px;
    background: var(--navy);
    padding: 12px 0 0 40px;
    font-family: "Arimo", sans-serif; font-size: 14.5px; color: #fff;
  }
  .contact-band li {
    list-style: none; display: flex; align-items: center; gap: 10px;
    height: 23px;
  }
  .contact-band svg { width: 14px; height: 14px; flex: none; }
  .address {
    position: absolute; left: 66px; top: 236px;
    font-family: "Arimo", sans-serif; font-size: 16px; line-height: 1.35;
    color: var(--ink);
  }
  .accent-square {
    position: absolute; right: 32px; top: 0;
    width: 74px; height: 52px; background: var(--sky);
  }
  .brand-name {
    position: absolute; left: 340px; top: 118px;
    font-family: "Archivo Black", sans-serif;
    font-size: 40px; letter-spacing: 1px; color: var(--navy);
  }

  /* Back */
  .card--back {
    background: linear-gradient(200deg, var(--back-top) 0%, var(--back-bottom) 100%);
    display: flex; align-items: center; justify-content: center;
  }
  .brand-name--large {
    position: static;
    font-size: 68px; letter-spacing: 3px; color: #fff;
  }
</style>
</head>
<body>
<main class="canvas">
  <section class="card card--front" aria-label="Card front">
    <div class="accent-square"></div>
    <div class="holder">
      <p class="holder__name">Warren Halbeck</p>
      <p class="holder__role">General Manager</p>
    </div>
    <ul class="contact-band">
      <li>
        <svg viewBox="0 0 24 24" fill="var(--sky)" aria-hidden="true"><path d="M6.6 10.8a15 15 0 0 0 6.6 6.6l2.2-2.2a1 1 0 0 1 1-.25 11.4 11.4 0 0 0 3.6.57 1 1 0 0 1 1 1V20a1 1 0 0 1-1 1A17 17 0 0 1 3 4a1 1 0 0 1 1-1h3.5a1 1 0 0 1 1 1c0 1.25.2 2.45.57 3.57a1 1 0 0 1-.25 1z"/></svg>
        0472 915 348
      </li>
      <li>
        <svg viewBox="0 0 24 24" fill="var(--sky)" aria-hidden="true"><path d="M2 5h20v14H2z" opacity=".9"/><path d="M2 5l10 8 10-8" stroke="var(--navy)" stroke-width="2" fill="none"/></svg>
        Warren.halbeck@tovrin.com.au
      </li>
      <li>
        <svg viewBox="0 0 24 24" fill="none" stroke="var(--sky)" stroke-width="2" aria-hidden="true"><circle cx="12" cy="12" r="9"/><path d="M3 12h18M12 3c3 3 3 15 0 18M12 3c-3 3-3 15 0 18"/></svg>
        www.tovrin.com.au
      </li>
    </ul>
    <address class="address" style="font-style:normal">
      87 Marrow Ave<br>Pendlebay, QLD, 4023
    </address>
    <p class="brand-name">TOVRIN</p>
  </section>

  <section class="card card--back" aria-label="Card back">
    <p class="brand-name brand-name--large">TOVRIN</p>
  </section>
</main>
</body>
</html>
```